Loan Application Project

We have a bank application form in pdf and we wish to use the content of the application to develop a loan application using our own brand and look / feel with the brand of a Partner.

The content of the application can be simply copied across. We assume that the process for doing this is easy when armed with the right pdf software.
Updates

Hi - I have now added both the second logo that needs incorporating and also gone through and made changes to the text on the actual application form so this project is now ready to "bring home".  Thanks Gerald

Target Market(s)

Samll Business Operators

Industry/Entity Type

Bank

Requirements
Must have
• Must remove all reference to Coastal Meridian Bank or CMB and replace with Tolvane Financial Services Pty Ltd (Tolvane). I'd be happy to go through the hard copy and scan a copy where I have hand written changes for the designer
Nice to have
• To be able to electronically complete the form would be great. Not sure how you do this but I know it can be done for pdf forms.

```html
<!DOCTYPE html>
<html lang="en">
<head>
<meta charset="utf-8">
<title>Entity 4 – Individual</title>
<link href="https://fonts.googleapis.com/css2?family=Source+Sans+3:wght@400;600;700&display=swap" rel="stylesheet">
<style>
:root{
  --ink:#231f20;
  --panel:#e5efee;
  --field:#ffffff;
  --rule:#6f7173;
  --bar:#000000;
}
*{box-sizing:border-box;margin:0;padding:0}
html,body{width:849px;height:1200px;overflow:hidden;background:#fff}
body{position:relative;font-family:"Source Sans 3",Arial,sans-serif;color:var(--ink);font-size:10px}
.top-bar{position:absolute;left:40px;top:40px;width:768px;height:17px;background:var(--bar)}
.form-panel{position:absolute;left:40px;top:57px;width:768px;height:1103px;background:var(--panel)}
.section-title{position:absolute;left:51px;top:69px;font-size:13.5px;font-weight:700;line-height:17px;display:flex;align-items:center}
.section-title .marker{width:24px;height:15px;background:var(--bar);margin-right:6px}
.title-rule{position:absolute;left:51px;top:68px;width:747px;height:1px;background:var(--rule)}
.lbl{position:absolute;line-height:12px;white-space:nowrap}
.heading{position:absolute;font-weight:700;font-size:11px;line-height:13px;white-space:nowrap}
.field{position:absolute;background:var(--field);border:1px solid var(--rule);height:20px}
.field .sep{position:absolute;top:3px;line-height:12px}
.field.address{height:60px}
.field.address::before,.field.address::after{content:"";position:absolute;left:4px;right:0;height:1px;background:var(--rule)}
.field.address::before{top:19px}
.field.address::after{top:39px}
.field.address .sub{position:absolute;top:45px;line-height:12px}
.field.details{height:40px}
.field.details::before{content:"";position:absolute;left:4px;right:0;top:19px;height:1px;background:var(--rule)}
.check{position:absolute;display:flex;align-items:center;gap:5px;white-space:nowrap;line-height:12px}
.check::before{content:"";width:11px;height:11px;background:var(--field);border:1px solid var(--rule);flex:none}
.page-no{position:absolute;right:41px;top:1163px;font-size:9.5px}
</style>
</head>
<body>
<div class="top-bar"></div>
<div class="form-panel"></div>
<div class="title-rule"></div>
<div class="section-title"><span class="marker"></span>Entity 4 – Individual</div>

<!-- Left column -->
<span class="check" style="left:52px;top:104px">Borrower</span>
<span class="check" style="left:162px;top:104px">Guarantor</span>
<span class="check" style="left:52px;top:123px">Mr</span>
<span class="check" style="left:106px;top:123px">Mrs</span>
<span class="check" style="left:161px;top:123px">Miss</span>
<span class="check" style="left:221px;top:123px">Ms</span>
<span class="lbl" style="left:51px;top:144px">Other</span>
<div class="field" style="left:95px;top:139px;width:178px"></div>
<span class="lbl" style="left:51px;top:164px">Surname</span>
<div class="field" style="left:50px;top:180px;width:365px"></div>
<span class="lbl" style="left:51px;top:204px">Given name(s)</span>
<div class="field" style="left:50px;top:219px;width:365px"></div>
<span class="lbl" style="left:51px;top:245px">Date of Birth</span>
<span class="lbl" style="left:193px;top:245px">Drivers License Number</span>
<div class="field" style="left:50px;top:261px;width:135px"><span class="sep" style="left:48px">/</span><span class="sep" style="left:90px">/</span></div>
<div class="field" style="left:192px;top:261px;width:223px"></div>
<span class="lbl" style="left:51px;top:290px">Driver's Licence Country</span>
<span class="check" style="left:224px;top:289px">AU</span>
<span class="check" style="left:281px;top:289px">NZ</span>
<span class="check" style="left:335px;top:289px">Other</span>
<span class="lbl" style="left:51px;top:310px">Permanent Australian Resident?</span>
<span class="check" style="left:224px;top:308px">Yes</span>
<span class="check" style="left:281px;top:308px">No</span>
<span class="heading" style="left:51px;top:331px">Marital Status</span>
<span class="check" style="left:52px;top:350px">Single</span>
<span class="check" style="left:133px;top:350px">Married (Provide spouse name below)</span>
<span class="check" style="left:353px;top:350px">Divorced</span>
<span class="check" style="left:52px;top:370px">Seperated</span>
<span class="check" style="left:133px;top:370px">Widowed</span>
<span class="check" style="left:224px;top:370px">Defacto (Provide partner name below)</span>
<span class="check" style="left:52px;top:389px">Other (Provide details below)</span>
<div class="field" style="left:50px;top:405px;width:365px"></div>
<span class="lbl" style="left:51px;top:436px">Date of last change in marital status</span>
<div class="field" style="left:232px;top:431px;width:135px"><span class="sep" style="left:48px">/</span><span class="sep" style="left:89px">/</span></div>
<span class="lbl" style="left:51px;top:457px">Ages of your dependent children</span>
<div class="field" style="left:50px;top:477px;width:62px"></div>
<div class="field" style="left:119px;top:477px;width:62px"></div>
<div class="field" style="left:188px;top:477px;width:62px"></div>
<div class="field" style="left:257px;top:477px;width:61px"></div>
<div class="field" style="left:325px;top:477px;width:61px"></div>
<span class="heading" style="left:51px;top:507px">Contact details</span>
<span class="lbl" style="left:51px;top:528px">Home telephone number</span>
<div class="field" style="left:50px;top:544px;width:178px"><span class="sep" style="left:14px">(&nbsp;&nbsp;&nbsp;&nbsp;)</span></div>
<span class="lbl" style="left:51px;top:572px">Is this a silent number?</span>
<span class="check" style="left:183px;top:571px">Yes</span>
<span class="check" style="left:237px;top:571px">No</span>
<span class="lbl" style="left:51px;top:594px">Work telephone number</span>
<span class="lbl" style="left:237px;top:594px">Mobile number</span>
<div class="field" style="left:50px;top:609px;width:178px"><span class="sep" style="left:14px">(&nbsp;&nbsp;&nbsp;&nbsp;)</span></div>
<div class="field" style="left:237px;top:609px;width:178px"><span class="sep" style="left:14px">(&nbsp;&nbsp;&nbsp;&nbsp;)</span></div>
<span class="lbl" style="left:51px;top:635px">Email address</span>
<span class="lbl" style="left:237px;top:635px">Facsimile number</span>
<div class="field" style="left:50px;top:650px;width:178px"></div>
<div class="field" style="left:237px;top:650px;width:178px"><span class="sep" style="left:14px">(&nbsp;&nbsp;&nbsp;&nbsp;)</span></div>
<span class="lbl" style="left:51px;top:675px">Home address</span>
<div class="field address" style="left:50px;top:690px;width:365px"><span class="sub" style="left:12px">State</span><span class="sub" style="left:112px">Postcode</span><span class="sub" style="left:226px">Country</span></div>
<span class="lbl" style="left:51px;top:755px">Postal address (if different to above)</span>
<div class="field address" style="left:50px;top:770px;width:365px"><span class="sub" style="left:12px">State</span><span class="sub" style="left:112px">Postcode</span><span class="sub" style="left:226px">Country</span></div>
<span class="heading" style="left:51px;top:836px;font-size:10px;line-height:11px">Have you provided guarantees or security to support any other borrowings<br>at other financial institutions?</span>
<span class="check" style="left:52px;top:865px">Yes – give details</span>
<span class="check" style="left:178px;top:865px">No</span>
<div class="field details" style="left:50px;top:882px;width:365px"></div>
<span class="heading" style="left:51px;top:933px">Residential details</span>
<span class="check" style="left:52px;top:953px">Owner – No Mortgage</span>
<span class="check" style="left:198px;top:953px">Owner – with Mortgage</span>
<span class="check" style="left:358px;top:953px">Renting</span>
<span class="check" style="left:52px;top:972px">Boarding</span>
<span class="check" style="left:140px;top:972px">Living with Relatives</span>
<span class="check" style="left:280px;top:972px">Supplied by Employer</span>
<span class="lbl" style="left:51px;top:992px">Name of Owner/Agent</span>
<div class="field" style="left:50px;top:1007px;width:365px"></div>
<span class="lbl" style="left:51px;top:1034px">Telephone number</span>
<div class="field" style="left:50px;top:1049px;width:178px"><span class="sep" style="left:14px">(&nbsp;&nbsp;&nbsp;&nbsp;)</span></div>
<span class="lbl" style="left:51px;top:1084px">When did you move to the above address?</span>
<div class="field" style="left:260px;top:1079px;width:135px"><span class="sep" style="left:48px">/</span><span class="sep" style="left:89px">/</span></div>

<!-- Right column -->
<span class="lbl" style="left:434px;top:100px">Previous Home address (if under 3 years at present home)</span>
<div class="field address" style="left:434px;top:116px;width:364px"><span class="sub" style="left:12px">State</span><span class="sub" style="left:112px">Postcode</span><span class="sub" style="left:226px">Country</span></div>
<span class="lbl" style="left:434px;top:191px">Lived there for</span>
<div class="field" style="left:522px;top:186px;width:62px"></div>
<span class="lbl" style="left:611px;top:191px">Years</span>
<div class="field" style="left:660px;top:186px;width:62px"></div>
<span class="lbl" style="left:743px;top:191px">Months</span>
<span class="heading" style="left:434px;top:214px">Employment details</span>
<span class="check" style="left:436px;top:233px">Full-time</span>
<span class="check" style="left:528px;top:233px">Part-time</span>
<span class="check" style="left:620px;top:233px">Self employed</span>
<span class="lbl" style="left:434px;top:253px">Other</span>
<div class="field" style="left:478px;top:248px;width:180px"></div>
<span class="lbl" style="left:434px;top:274px">Employer's Name</span>
<div class="field" style="left:434px;top:288px;width:364px"></div>
<span class="lbl" style="left:434px;top:314px">Occupation</span>
<div class="field" style="left:434px;top:329px;width:364px"></div>
<span class="lbl" style="left:434px;top:354px">Type of Industry</span>
<div class="field" style="left:434px;top:369px;width:364px"></div>
<span class="lbl" style="left:434px;top:395px">When did you commence work with this employer?</span>
<div class="field" style="left:434px;top:410px;width:135px"><span class="sep" style="left:48px">/</span><span class="sep" style="left:89px">/</span></div>
<span class="lbl" style="left:434px;top:436px">Time in Industry</span>
<div class="field" style="left:434px;top:451px;width:364px"></div>
<span class="lbl" style="left:434px;top:476px">Previous employment (if under 3 years with present employer)</span>
<div class="field" style="left:434px;top:490px;width:364px"></div>
<span class="lbl" style="left:434px;top:516px">Previous employer</span>
<div class="field" style="left:434px;top:530px;width:364px"></div>
<span class="lbl" style="left:434px;top:562px">Worked there</span>
<div class="field" style="left:522px;top:557px;width:62px"></div>
<span class="lbl" style="left:611px;top:562px">Years</span>
<div class="field" style="left:660px;top:557px;width:62px"></div>
<span class="lbl" style="left:743px;top:562px">Months</span>
<span class="heading" style="left:434px;top:585px">Reference</span>
<span class="lbl" style="left:434px;top:604px">Has there ever been or are there now any judgements, attachments or<br>legal proceedings against you?</span>
<span class="check" style="left:436px;top:636px">Yes – give details</span>
<span class="check" style="left:561px;top:636px">No</span>
<div class="field details" style="left:434px;top:652px;width:364px"></div>
<span class="heading" style="left:434px;top:703px">Details of nearest relative not living with you</span>
<span class="lbl" style="left:434px;top:724px">Name</span>
<div class="field" style="left:434px;top:738px;width:364px"></div>
<span class="lbl" style="left:434px;top:765px">Relationship</span>
<span class="lbl" style="left:621px;top:765px">Telephone number</span>
<div class="field" style="left:434px;top:780px;width:178px"></div>
<div class="field" style="left:620px;top:780px;width:178px"><span class="sep" style="left:14px">(&nbsp;&nbsp;&nbsp;&nbsp;)</span></div>
<span class="lbl" style="left:434px;top:805px">Address</span>
<div class="field address" style="left:434px;top:820px;width:364px"><span class="sub" style="left:12px">State</span><span class="sub" style="left:112px">Postcode</span><span class="sub" style="left:226px">Country</span></div>

<span class="page-no">Page 5 of 14</span>
</body>
</html>
```